Dental Savings Plan - Raymond Castell DDS

We need a tri-fold brochure and 1 page flyer/poster for Dr. Raymond Castell' dental office located on Maui, Hawaii. We are offering a new "Dental Savings Plan" to patients.
I have included 3 photos, along with the office logo. You do not have to use all photos if you do not want to. We want this to catch the eyes of patients, easy for them to read and understand, and to show them that this is a much better option than dental insurance.
Please use same Hawaiian theme and colors on the office website https://www.brightcoveclinic.com .

Please also include the following to promote this new plan:

Dental Services Include
• Professional Dental Cleanings (2 per benefit year)
• Perio Maintenance Cleanings (3 per benefit year) covered at 80%
• Radiographs as needed (1 set of X-rays per benefit year)
• Doctor Examinations (2 per benefit year)
• Ozone Treatment
• BRISK Amalgam Removal
• Additional limited/emergency exam (1 per benefit year)
• Cosmetic consultation
• 15% discount on all other services (including cosmetic procedures)
• 10% discount on implants and implant crowns

Advantages of the Dental Savings Plan
1. No deductibles
2. No waiting periods
3. No claims to file
4. No frequency limitations or exclusions
5. No yearly maximum benefits
6. No pre-authorization requirements
7. No pre-existing conditions limitations
8. State of the art facility and technology
9. Immediate enrollment
10. Highest quality of care for you and your Ohana

Annual Fee
$399 first family member/individual (equivalent to $33 per month)
$349 second family member (equivalent to $29 per month)
$249 each additional family member (equivalent to $20 per month)

Provisions of the Dental Savings Plan
• May not be combined with insurance plans, discounts or promotions
• This Dental Savings Plan is not an insurance plan, but a payment arrangement provided by Raymond Castell DDS, and is not transferable to any other dental office or dental specialist
• Payment for services are due at the date of service
• This program is for you and is not transferable
• Benefits are provided for one year from the date the plan is purchased
• Must be paid in full when starting the plan
• No refunds will be provided for dues of the plan annual fee under any circumstances, including failure to schedule and maintain appointments
• If Pay Ladder is used to pay for the program and for services then only a 10% discount will be given
• To receive the full 15% discount on restorative treatment, you must schedule the appointment the day it is recommended. Any failed appointment results in the loss of the 15% discount.

Target Market(s)

Dental patients without dental insurance

Industry/Entity Type

Dental Clinic

Requirements
Must have
• My project must have the logo file to identify the dental office, Hawaiian theme, same colors as website, match style of website font, theme and colors, as well as, all the Dental Services, Advantages of the Dental Savings Plan, Annual Fee, and the Provisions of the Dental Savings Plan.

```html
<!DOCTYPE html>
<html lang="en">
<head>
<meta charset="utf-8">
<title>Dental Savings Plan – Raymond Castell DDS</title>
<link href="https://fonts.googleapis.com/css2?family=Encode+Sans+Condensed:wght@400;600;700&family=Open+Sans:ital,wght@0,400;0,600;0,700;1,600;1,800&display=swap" rel="stylesheet">
<style>
  :root{
    --stage:#e4e4e4;
    --ink-dark:#3a3a3a;
    --ink-darker:#2f2f2f;
    --aloha-blue:#1ea5e0;
    --aloha-green:#8dc63f;
    --paper:#ffffff;
    --body-grey:#222;
    --muted:#d9d9d9;
  }
  *{box-sizing:border-box;margin:0;padding:0}
  html,body{width:1200px;height:923px;overflow:hidden;background:var(--stage)}
  body{position:relative;font-family:"Open Sans",sans-serif}
  .spread{position:absolute;top:235px;width:585px;height:452px;display:flex;box-shadow:0 6px 18px rgba(0,0,0,.18)}
  .spread--outside{left:8px}
  .spread--inside{left:607px}
  .panel{position:relative;width:195px;height:100%;overflow:hidden}

  /* outside */
  .photo{position:absolute;left:0;width:100%}
  .fee-panel{background:var(--ink-dark);color:#fff}
  .fee-panel .photo{top:0;height:150px;background:linear-gradient(135deg,#f4f4f4,#e3d6cf 55%,#cfcfcf)}
  .fee-title{position:absolute;top:168px;left:18px;font-style:italic;font-weight:800;font-size:22px;color:var(--aloha-blue)}
  .fee-list{position:absolute;top:206px;left:18px;right:10px;list-style:none}
  .fee-list li{font-size:9.5px;font-style:italic;line-height:1.35;margin-bottom:14px}
  .fee-list b{font-size:12px;font-weight:800}
  .offer-panel{background:var(--aloha-blue)}
  .offer-panel .photo{top:0;height:290px;background:linear-gradient(180deg,#3d8fd6 0%,#8cc4ec 40%,#27b5cf 62%,#0f7fa8 100%)}
  .offer-text{position:absolute;top:308px;left:10px;right:10px;text-align:center;color:#fff;font-weight:600;font-size:17px;line-height:1.25}
  .offer-text em{display:block;font-style:italic;font-weight:800;color:var(--aloha-green)}
  .contact-panel{background:var(--paper)}
  .brand{position:absolute;top:40px;left:0;right:0;text-align:center}
  .brand-mark{display:block;width:30px;height:30px;border-radius:50%;background:var(--aloha-green);margin:0 auto 8px}
  .brand-name{font-family:"Encode Sans Condensed",sans-serif;font-weight:700;font-size:20px;color:var(--aloha-blue)}
  .contact-panel .photo{top:150px;height:170px;background:linear-gradient(120deg,#d6dde3,#eef1f3 45%,#3a4b66 75%,#1d2838)}
  .contact-block{position:absolute;left:0;right:0;top:320px;bottom:0;background:var(--ink-darker);color:#fff;padding:14px 0 0 18px}
  .contact-list{list-style:none}
  .contact-list li{display:flex;align-items:center;gap:7px;font-size:9px;margin-bottom:6px}
  .contact-list svg{flex:none}
  .social{display:flex;gap:10px;margin-top:12px}
  .social span{width:24px;height:24px;border:1.5px solid #fff;display:flex;align-items:center;justify-content:center}

  /* inside */
  .services-panel{background:var(--ink-dark);color:#fff;padding:18px 12px 0 14px}
  .advantages-panel{background:var(--aloha-blue);color:#fff;padding:18px 12px 0 16px}
  .provisions-panel{background:var(--paper);color:var(--body-grey);padding:18px 12px 0 14px}
  .heading{font-family:"Encode Sans Condensed",sans-serif;font-weight:700;font-size:19px;line-height:1.05;margin-bottom:14px}
  .provisions-panel .heading{color:var(--aloha-blue);font-size:18px}
  .cond{font-family:"Encode Sans Condensed",sans-serif}
  .service-list{list-style:none}
  .service-list li{font-size:8.6px;line-height:1.3;margin-bottom:11px;padding-left:8px;position:relative}
  .service-list li::before{content:"•";position:absolute;left:0}
  .advantage-list{list-style:none;counter-reset:adv}
  .advantage-list li{font-size:8.6px;line-height:1.3;margin-bottom:16px;padding-left:14px;position:relative;counter-increment:adv}
  .advantage-list li::before{content:counter(adv)".";position:absolute;left:0}
  .provision-list{list-style:none;margin-top:6px}
  .provision-list li{font-size:7.2px;font-weight:600;line-height:1.28;margin-bottom:9px;padding-left:7px;position:relative}
  .provision-list li::before{content:"•";position:absolute;left:0}
  .badge{position:absolute;border-radius:50%;background:var(--aloha-blue)}
  .badge--services{width:34px;height:34px;left:80px;bottom:20px}
  .badge--provisions{width:50px;height:50px;right:12px;top:14px}
  .wave{position:absolute;left:0;bottom:0;width:100%;height:40px}
</style>
</head>
<body>

<section class="spread spread--outside" aria-label="Brochure outside">
  <div class="panel fee-panel">
    <div class="photo" role="img" aria-label="Photo of a patient smiling during a dental check-up"></div>
    <h2 class="fee-title">Annual Fee</h2>
    <ul class="fee-list">
      <li><b>$399</b> first family member/individual (equivalent to $33 per month)</li>
      <li><b>$349</b> second family member (equivalent to $29 per month)</li>
      <li><b>$249</b> each additional family member (equivalent to $20 per month)</li>
    </ul>
  </div>
  <div class="panel offer-panel">
    <div class="photo" role="img" aria-label="Photo of a palm tree over a turquoise Hawaiian sea"></div>
    <p class="offer-text">We are offering<br>a new<em>"Dental Savings Plan"</em>to patients</p>
  </div>
  <div class="panel contact-panel">
    <div class="brand">
      <span class="brand-mark"></span>
      <span class="brand-name">Raymond Castell DDS</span>
    </div>
    <div class="photo" role="img" aria-label="Photo of the dentist smiling beside X-ray monitors"></div>
    <div class="contact-block">
      <ul class="contact-list">
        <li><svg width="11" height="11" viewBox="0 0 12 12"><circle cx="6" cy="6" r="5.3" fill="none" stroke="#fff"/><path d="M4 3.5l1 1.4-.6.7a4 4 0 0 0 2 2l.7-.6 1.4 1-.6.9C5.8 8.8 3.2 6.2 3.1 4.1z" fill="#fff"/></svg>808-555-0172</li>
        <li><svg width="11" height="11" viewBox="0 0 12 12"><circle cx="6" cy="6" r="5.3" fill="none" stroke="#fff"/><rect x="3" y="4" width="6" height="4" fill="none" stroke="#fff" stroke-width=".8"/><path d="M3 4l3 2.2L9 4" fill="none" stroke="#fff" stroke-width=".8"/></svg>hello@brightcoveclinic.com</li>
        <li><svg width="11" height="11" viewBox="0 0 12 12"><circle cx="6" cy="6" r="5.3" fill="none" stroke="#fff"/><circle cx="6" cy="6" r="2.4" fill="none" stroke="#fff" stroke-width=".8"/><path d="M3.6 6h4.8M6 3.6v4.8" stroke="#fff" stroke-width=".6"/></svg>www.brightcoveclinic.com</li>
        <li><svg width="11" height="11" viewBox="0 0 12 12"><circle cx="6" cy="6" r="5.3" fill="none" stroke="#fff"/><path d="M6 9.2S3.9 6.8 3.9 5.2a2.1 2.1 0 0 1 4.2 0C8.1 6.8 6 9.2 6 9.2z" fill="#fff"/></svg>4410 Coral Ln # 12, Kihei, HI 96753</li>
      </ul>
      <div class="social">
        <span></span>
        <span></span>
        <span><svg width="10" height="13" viewBox="0 0 10 13"><path d="M5 12.5S1 8 1 5a4 4 0 0 1 8 0c0 3-4 7.5-4 7.5z" fill="#fff"/><circle cx="5" cy="5" r="1.5" fill="#2f2f2f"/></svg></span>
      </div>
    </div>
  </div>
</section>

<section class="spread spread--inside" aria-label="Brochure inside">
  <div class="panel services-panel">
    <h2 class="heading">Dental Services Include</h2>
    <ul class="service-list cond">
      <li>Professional Dental Cleanings<br>(2 per benefit year)</li>
      <li>Perio Maintenance Cleanings<br>(3 per benefit year) covered at 80%</li>
      <li>Radiographs as needed<br>(1 set of X-rays per benefit year)</li>
      <li>Doctor Examinations<br>(2 per benefit year)</li>
      <li>Ozone Treatment</li>
      <li>BRISK Amalgam Removal</li>
      <li>Additional limited/emergency exam<br>(1 per benefit year)</li>
      <li>Cosmetic consultation</li>
      <li>15% discount on all other services<br>(including cosmetic procedures)</li>
      <li>10% discount on implants and implant crowns</li>
    </ul>
    <span class="badge badge--services"></span>
  </div>
  <div class="panel advantages-panel">
    <h2 class="heading">Advantages of the<br>Dental Savings Plan</h2>
    <ol class="advantage-list cond">
      <li>No deductibles</li>
      <li>No waiting periods</li>
      <li>No claims to file</li>
      <li>No frequency limitations or exclusions</li>
      <li>No yearly maximum benefits</li>
      <li>No pre-authorization requirements</li>
      <li>No pre-existing conditions limitations</li>
      <li>State of the art facility and technology</li>
      <li>Immediate enrollment</li>
      <li>Highest quality of care for you<br>and your Ohana</li>
    </ol>
  </div>
  <div class="panel provisions-panel">
    <h2 class="heading">Provisions<br>of the Dental<br>Savings Plan</h2>
    <span class="badge badge--provisions"></span>
    <ul class="provision-list cond">
      <li>May not be combined with insurance plans, discounts or promotions</li>
      <li>This Dental Savings Plan is not an insurance plan, but a payment arrangement provided by Raymond Castell DDS, and is not transferable to any other dental office or dental specialist</li>
      <li>Payment for services are due at the date of service</li>
      <li>This program is for you and is not transferable</li>
      <li>Benefits are provided for one year from the date the plan is purchased</li>
      <li>Must be paid in full when starting the plan</li>
      <li>No refunds will be provided for dues of the plan annual fee under any circumstances, including failure to schedule and maintain appointments</li>
      <li>If Pay Ladder is used to pay for the program and for services then only a 10% discount will be given</li>
      <li>To receive the full 15% discount on restorative treatment, you must schedule the appointment the day it is recommended. Any failed appointment results in the loss of the 15% discount.</li>
    </ul>
    <svg class="wave" viewBox="0 0 195 40" preserveAspectRatio="none" aria-hidden="true"><path d="M0 40 L0 34 C70 34 150 20 195 0 L195 40 Z" fill="#3a3a3a"/></svg>
  </div>
</section>

</body>
</html>
```